BrindleStaffing Business Card Design

We are a staffing company finding positions for dedicated nurses and physicians.

Target Market(s)

Business Professionals

Industry/Entity Type

Staffing

Contact Information for Business Card

Gordon Pratley
Chairman
417 39th Avenue South
SAINT PETERSBURG FL 33712
813-555-4172 Mobile
813-555-8036 Fax
gpratley@brindlestaffing.com
www.brindlestaffing.com

Font styles to use
Sans Serif

Colors
fbee3e
f04a50
f37122

Requirements
Must have
• Logo Attached, see colors below. We'd like to see Yellow, Orange and Red.

```html
<!DOCTYPE html>
<html lang="en">
<head>
<meta charset="utf-8">
<title>BrindleStaffing Business Card</title>
<link href="https://fonts.googleapis.com/css2?family=Roboto:wght@400;500;700&display=swap" rel="stylesheet">
<style>
  :root {
    --backdrop: #2b2b2b;
    --card-white: #ffffff;
    --brand-red: #f04a50;
    --brand-orange: #f37122;
    --brand-yellow: #fbee3e;
    --text-grey: #555a60;
    --divider: #c9c9c9;
    --on-orange: #ffffff;
  }
  html, body {
    margin: 0;
    padding: 0;
    width: 1125px;
    height: 1200px;
    overflow: hidden;
    background: var(--backdrop);
    font-family: "Roboto", Arial, sans-serif;
  }
  .canvas {
    position: relative;
    width: 1125px;
    height: 1200px;
  }
  .card {
    position: absolute;
    left: 150px;
    width: 826px;
    height: 472px;
    overflow: hidden;
  }
  .card-front { top: 98px; background: var(--card-white); }
  .card-back { top: 631px; background: var(--brand-orange); }

  .front-wordmark {
    position: absolute;
    left: 52px;
    top: 208px;
    font-size: 52px;
    font-weight: 700;
    letter-spacing: -0.8px;
    color: var(--brand-red);
    line-height: 1;
  }
  .divider {
    position: absolute;
    left: 441px;
    top: 108px;
    width: 1px;
    height: 264px;
    background: var(--divider);
  }
  .details {
    position: absolute;
    left: 477px;
    top: 110px;
    color: var(--text-grey);
  }
  .person-name {
    margin: 0;
    font-size: 31px;
    font-weight: 700;
    color: var(--brand-red);
    line-height: 1.1;
  }
  .person-title {
    margin: 2px 0 0 2px;
    font-size: 21px;
    font-weight: 500;
    color: var(--brand-orange);
    line-height: 1.1;
  }
  .address {
    margin: 16px 0 0 0;
    font-size: 20px;
    line-height: 25px;
    font-style: normal;
  }
  .contact-list {
    list-style: none;
    margin: 14px 0 0 0;
    padding: 0;
    font-size: 20px;
  }
  .contact-list li {
    display: flex;
    align-items: center;
    height: 26.5px;
  }
  .contact-list svg {
    width: 20px;
    height: 20px;
    margin-right: 13px;
    flex: none;
  }
  .rule-yellow {
    position: absolute;
    left: 0;
    top: 444px;
    width: 100%;
    height: 3px;
    background: var(--brand-yellow);
  }
  .band-red {
    position: absolute;
    left: 0;
    top: 450px;
    width: 100%;
    height: 22px;
    background: var(--brand-red);
  }

  .back-brand {
    position: absolute;
    right: 47px;
    top: 358px;
    text-align right;
    text-align: right;
    color: var(--on-orange);
  }
  .back-wordmark {
    font-size: 40px;
    font-weight: 700;
    letter-spacing: -0.6px;
    line-height: 1;
  }
  .back-web {
    margin-top: 10px;
    font-size: 19px;
    letter-spacing: 2px;
  }
</style>
</head>
<body>
<div class="canvas">
  <section class="card card-front">
    <div class="front-wordmark">BrindleStaffing</div>
    <div class="divider"></div>
    <div class="details">
      <h1 class="person-name">Gordon Pratley</h1>
      <p class="person-title">Chairman</p>
      <address class="address">417 39th Avenue South<br>SAINT PETERSBURG FL 33712</address>
      <ul class="contact-list">
        <li>
          <svg viewBox="0 0 20 20" aria-hidden="true"><rect x="5" y="1" width="10" height="18" rx="2" fill="var(--brand-red)"/><rect x="7" y="4" width="6" height="10" fill="#fff"/><circle cx="10" cy="16.3" r="1" fill="#fff"/></svg>
          <span>813-555-4172</span>
        </li>
        <li>
          <svg viewBox="0 0 20 20" aria-hidden="true"><rect x="5" y="2" width="10" height="5" fill="var(--brand-red)"/><rect x="1" y="7" width="18" height="8" rx="1.5" fill="var(--brand-red)"/><rect x="4" y="12" width="12" height="6" fill="#fff" stroke="var(--brand-red)" stroke-width="1.5"/></svg>
          <span>813-555-8036</span>
        </li>
        <li>
          <svg viewBox="0 0 20 20" aria-hidden="true"><rect x="1" y="4" width="18" height="12" fill="var(--brand-red)"/><path d="M2 5 L10 11 L18 5" fill="none" stroke="#fff" stroke-width="1.5"/></svg>
          <span>gpratley@brindlestaffing.com</span>
        </li>
        <li>
          <svg viewBox="0 0 20 20" aria-hidden="true"><circle cx="10" cy="10" r="8.5" fill="var(--brand-red)"/><path d="M5 6 Q8 5 9 8 Q8 11 6 11 Q5 13 6 15 M12 4 Q11 7 13 8 Q16 8 15 11 Q13 13 14 16" fill="none" stroke="#fff" stroke-width="1.6"/></svg>
          <span>www.brindlestaffing.com</span>
        </li>
      </ul>
    </div>
    <div class="rule-yellow"></div>
    <div class="band-red"></div>
  </section>

  <section class="card card-back">
    <div class="back-brand">
      <div class="back-wordmark">BrindleStaffing</div>
      <div class="back-web">www.brindlestaffing.com</div>
    </div>
  </section>
</div>
</body>
</html>
```